New Business Card Design Project LORVANTI-Italy

we are LORVANTI-Italy
our company in the market for 3 years we are luxury cosmetic company and its about time for a facelift :)
i will like to have elegant luxurious and unique business card
that will give the person that get it a unique, luxurious and elegant impression
I'm VERY OPEN FOR NEW IDEAS , even duo i add a few files of things that i see on line and i like them

i add my logo as well
my website is LORVANTI.COM
(if you would like to see the main style that we have)

Target Market(s)

adult that have money :)

Industry/Entity Type

Business

Contact Information for Business Card

Name - Dario Lorvanti
Position - CEO and CO Founder
address - 4817 E Halvern
telephone - 555-384-1926
email - dario@lorvanti.com
fax - 555-384-1926
website - LORVANTI.COM

Colors
000000
959595
fbee3e
ffffff

Requirements
Must have
• big logo in GOLD color
• elegant look
• impressive
Nice to have
• not must but maybe classy pattern background
• not must but maybe emblem
• maybe clear plastic business card
Should not have
• colors
• images

```html
<!DOCTYPE html>
<html lang="en">
<head>
<meta charset="utf-8">
<title>LORVANTI Italy – Business Card</title>
<link rel="stylesheet" href="https://fonts.googleapis.com/css2?family=Tinos&family=PT+Sans&display=swap">
<style>
  :root {
    --backdrop: #000000;
    --card: #323337;
    --card-edge: #2c2d31;
    --gold: #d6aa3c;
    --ink-light: #e6e6e6;
  }
  * { margin: 0; padding: 0; box-sizing: border-box; }
  html, body {
    width: 1200px; height: 900px; overflow: hidden;
    background: var(--backdrop);
  }
  .stage { position: relative; width: 1200px; height: 900px; }
  .card {
    position: absolute; top: 271px; width: 457px; height: 281px;
    border-radius: 14px;
    background: radial-gradient(ellipse at 40% 35%, #37383c 0%, var(--card) 55%, var(--card-edge) 100%);
  }
  .card--front { left: 137px; }
  .card--back { left: 626px; }

  /* front: brand block */
  .brand-ring {
    position: absolute; left: 84px; top: 69px; width: 74px; height: 74px;
    border: 2px solid var(--gold); border-radius: 50%;
  }
  .brand-name {
    position: absolute; left: 40px; top: 153px; width: 162px;
    text-align: center; color: var(--gold);
    font-family: "Tinos", serif; font-size: 30px; letter-spacing: 0.5px;
  }
  .brand-rule {
    position: absolute; left: 40px; top: 195px; width: 162px; height: 2px;
    background: var(--gold);
  }
  .brand-origin {
    position: absolute; left: 40px; top: 201px; width: 162px;
    text-align: center; color: var(--gold);
    font-family: "Tinos", serif; font-size: 12px; letter-spacing: 1.5px;
  }
  .divider {
    position: absolute; left: 231px; top: 69px; width: 1px; height: 147px;
    background: linear-gradient(var(--gold), rgba(214,170,60,0.3));
  }

  /* front: contact block */
  .contact { position: absolute; left: 254px; top: 66px; }
  .contact__name {
    color: var(--gold); font-family: "Tinos", serif;
    font-size: 19px; line-height: 22px; letter-spacing: 0.3px;
  }
  .contact__role {
    color: var(--ink-light); font-family: "PT Sans", sans-serif;
    font-size: 13px; line-height: 18px;
  }
  .contact__list { list-style: none; margin-top: 11px; }
  .contact__item {
    display: flex; align-items: center; gap: 6px;
    color: var(--ink-light); font-family: "PT Sans", sans-serif;
    font-size: 13px; line-height: 16.5px;
  }
  .contact__item svg { width: 10px; height: 10px; fill: var(--gold); flex: none; }
  .contact__address {
    margin-top: 15px; padding-left: 3px;
    color: var(--ink-light); font-family: "PT Sans", sans-serif; font-size: 13px;
  }

  /* back */
  .emblem-ring {
    position: absolute; left: 153px; top: 64px; width: 152px; height: 152px;
    border: 3px solid var(--gold); border-radius: 50%;
    display: flex; align-items: center; justify-content: center;
  }
  .emblem-name {
    color: var(--gold); font-family: "Tinos", serif;
    font-size: 24px; letter-spacing: 1px;
  }
</style>
</head>
<body>
<main class="stage">
  <section class="card card--front" aria-label="Business card front">
    <div class="brand-ring"></div>
    <div class="brand-name">LORVANTI</div>
    <div class="brand-rule"></div>
    <div class="brand-origin">ITALY</div>
    <div class="divider"></div>

    <div class="contact">
      <div class="contact__name">DARIO LORVANTI</div>
      <div class="contact__role">CEO and CO Founder</div>
      <ul class="contact__list">
        <li class="contact__item">
          <svg viewBox="0 0 10 10" aria-hidden="true"><path d="M2 0.5 L3.6 2.6 L2.8 3.6 Q4 6 6.4 7.2 L7.4 6.4 L9.5 8 L8.4 9.5 Q4.5 9.3 1.5 5.5 Q0.4 3.6 0.5 1.6 Z"/></svg>
          555-384-1926
        </li>
        <li class="contact__item">
          <svg viewBox="0 0 10 10" aria-hidden="true"><rect x="2.5" y="0.5" width="5" height="3"/><rect x="0.5" y="3.5" width="9" height="6" rx="1"/></svg>
          555-384-1926
        </li>
        <li class="contact__item">
          <svg viewBox="0 0 10 10" aria-hidden="true"><path d="M0.5 2 H9.5 V8.5 H0.5 Z M0.8 2.3 L5 5.6 L9.2 2.3" stroke="#323337" stroke-width="0.8"/></svg>
          dario@lorvanti.com
        </li>
        <li class="contact__item">
          <svg viewBox="0 0 10 10" aria-hidden="true"><circle cx="5" cy="5" r="4.5"/><path d="M0.5 5 H9.5 M5 0.5 Q2.5 5 5 9.5 M5 0.5 Q7.5 5 5 9.5" stroke="#323337" stroke-width="0.7" fill="none"/></svg>
          www.lorvanti.com
        </li>
      </ul>
      <div class="contact__address">4817 E Halvern</div>
    </div>
  </section>

  <section class="card card--back" aria-label="Business card back">
    <div class="emblem-ring">
      <span class="emblem-name">LORVANTI</span>
    </div>
  </section>
</main>
</body>
</html>
```